Business Card Design Project

This is the first time we use our new logo. We need a business card that we can use both on our institutional corporate relationships and also that works for our staff that deals with consumers directly.

VELUNDA is a new company dedicated to empower consumers and to provide them with the best choices for specialized health care using the latest telemedicine technology (medicine at a distance via videoconference).

We want to print this cards in high quality materials and process. We will like designs that allow us to use UV spot varnish and other techniques that will differentiate us.

We are including Two different versions of Color logos. In addition we are including white over black background logos. Those can be used replacing the black for a color.

Please note this is the first time we will be creating any corporate materials with our new logo and colors.

Target Market(s)

34+ consumers of medium high and high socioeconomic levels.

Industry/Entity Type

Health

Requirements
Must have
• Our logo on its original colors
Should not have
• Any other graphical element or design that is not our logo

```html
<!DOCTYPE html>
<html lang="en">
<head>
<meta charset="utf-8">
<title>VELUNDA Business Card</title>
<link rel="stylesheet" href="https://fonts.googleapis.com/css2?family=Montserrat:wght@500;600;700&family=Arimo:wght@400&display=swap">
<style>
  :root {
    --sky: #56b3dc;
    --navy: #1b5a8c;
    --teal: #1aa38c;
    --paper: #ffffff;
    --backdrop: #e9e6e1;
    --divider: rgba(255,255,255,0.55);
  }
  * { margin: 0; padding: 0; box-sizing: border-box; }
  html, body { width: 1200px; height: 1057px; overflow: hidden; }
  body { background: var(--backdrop); position: relative; font-family: "Arimo", Arial, sans-serif; }

  .card { position: absolute; left: 160px; width: 880px; height: 490px; overflow: hidden; box-shadow: 0 6px 18px rgba(0,0,0,0.18); }
  .card-front { top: 30px; background: var(--paper); }
  .card-back { top: 545px; background: var(--sky); }

  /* front */
  .brand { position: absolute; left: 80px; top: 95px; display: flex; align-items: center; gap: 28px; }
  .brand-dot { width: 64px; height: 64px; border-radius: 50%; background: var(--teal); }
  .brand-name { font-family: "Montserrat", sans-serif; font-weight: 700; font-size: 84px; letter-spacing: 6px; color: var(--navy); line-height: 1; }
  .person { position: absolute; left: 300px; top: 198px; font-family: "Montserrat", sans-serif; font-size: 30px; font-weight: 700; color: var(--navy); }
  .person .title { color: var(--teal); font-weight: 500; font-size: 24px; }

  .rule { position: absolute; left: 0; right: 0; top: 250px; height: 3px; background: var(--navy); }
  .band { position: absolute; left: 0; right: 0; top: 258px; bottom: 0; background: var(--sky); }

  .address { position: absolute; right: 470px; top: 38px; text-align: right; color: var(--paper); font-size: 21px; line-height: 32px; }
  .band-divider { position: absolute; left: 430px; top: 30px; width: 1px; height: 120px; background: var(--divider); }
  .contacts { position: absolute; left: 455px; top: 24px; list-style: none; color: var(--paper); font-size: 21px; line-height: 32px; }
  .contacts li { display: flex; align-items: center; gap: 10px; }
  .contacts svg { width: 18px; height: 18px; flex: none; }

  /* back */
  .back-mark { position: absolute; left: 0; right: 0; top: 150px; display: flex; justify-content: center; align-items: center; gap: 26px; }
  .back-dot { width: 80px; height: 80px; border-radius: 50%; border: 10px solid var(--paper); }
  .back-name { font-family: "Montserrat", sans-serif; font-weight: 700; font-size: 92px; letter-spacing: 8px; color: var(--paper); line-height: 1; }
  .back-url { position: absolute; left: 0; right: 0; top: 380px; text-align: center; font-family: "Montserrat", sans-serif; font-weight: 600; font-size: 28px; letter-spacing: 9px; color: var(--paper); }
</style>
</head>
<body>

<section class="card card-front">
  <div class="brand">
    <span class="brand-dot"></span>
    <span class="brand-name">VELUNDA</span>
  </div>
  <p class="person">Your Name, <span class="title">Title</span></p>
  <div class="rule"></div>
  <div class="band">
    <address class="address" style="font-style:normal">
      Street Name<br>City Name<br>State, City Zip Code
    </address>
    <div class="band-divider"></div>
    <ul class="contacts">
      <li>
        <svg viewBox="0 0 20 20" aria-hidden="true"><circle cx="10" cy="10" r="8.5" fill="none" stroke="#fff" stroke-width="1.6"/><path d="M7 5.5c-1 1-1 3.5 1.5 6s5 2.5 6 1.5l-1.6-1.6-1.4.8-3-3 .8-1.4z" fill="#fff"/></svg>
        012-555-0147
      </li>
      <li>
        <svg viewBox="0 0 20 20" aria-hidden="true"><circle cx="10" cy="10" r="8.5" fill="none" stroke="#fff" stroke-width="1.6"/><path d="M7 5.5c-1 1-1 3.5 1.5 6s5 2.5 6 1.5l-1.6-1.6-1.4.8-3-3 .8-1.4z" fill="#fff"/></svg>
        012-555-0147
      </li>
      <li>
        <svg viewBox="0 0 20 20" aria-hidden="true"><rect x="2" y="5" width="16" height="11" rx="1.5" fill="#fff"/><path d="M2.5 5.5 10 11l7.5-5.5" fill="none" stroke="#56b3dc" stroke-width="1.5"/></svg>
        name@velunda.com
      </li>
      <li>
        <svg viewBox="0 0 20 20" aria-hidden="true"><circle cx="10" cy="10" r="8" fill="none" stroke="#fff" stroke-width="1.6"/><ellipse cx="10" cy="10" rx="3.5" ry="8" fill="none" stroke="#fff" stroke-width="1.4"/><path d="M2 10h16M3.5 6h13M3.5 14h13" stroke="#fff" stroke-width="1.2"/></svg>
        www.velunda.com
      </li>
    </ul>
  </div>
</section>

<section class="card card-back">
  <div class="back-mark">
    <span class="back-dot"></span>
    <span class="back-name">VELUNDA</span>
  </div>
  <p class="back-url">www.velunda.com</p>
</section>

</body>
</html>
```